Tandem Hearth Works Pty Ltd

We need business cards for a company based in Perth, we install, service and maintain fire equipment.
On the front we want a great design with our logo and a small spot for our full company name, general company email address and office number. On the back we need space for our name, title, mobile number and email address on the back.

Target Market(s)

Facility managers and commercial/industrial building owners/occupiers.

Contact Information for Business Card

Font styles to use
Sans Serif

Requirements
Must have
• Please only submit 5 of your best samples.
Darker tones are preferred.
Nice to have
• We want to use, black, red and grey. Keep it modern and clean.
I've attached the company logo and a sample of a boarder we use on our emergency plans.
Should not have
• No preference. Let the designer choose.

```html
<!DOCTYPE html>
<html lang="en">
<head>
<meta charset="UTF-8">
<title>Tandem Hearth Works Pty Ltd – Business Card</title>
<link href="https://fonts.googleapis.com/css2?family=Montserrat:wght@700&family=Roboto:wght@400&display=swap" rel="stylesheet">
<style>
  :root {
    --backdrop: #3a3a3c;
    --card-black: #0d0d0e;
    --card-edge: #1a1a1b;
    --brand-red: #ec1c24;
    --wave-grey: #3b3b3d;
    --text-white: #f2f2f2;
    --emboss-grey: #222224;
    --muted-grey: #3c3c3e;
  }
  * { box-sizing: border-box; margin: 0; padding: 0; }
  html, body {
    width: 1200px; height: 1200px; overflow: hidden;
    background: var(--backdrop);
  }
  .canvas {
    width: 1200px; height: 1200px;
    display: flex; flex-direction: column; align-items: center; justify-content: center;
    gap: 50px;
  }
  .card {
    position: relative;
    width: 860px; height: 491px;
    border-radius: 28px;
    background: var(--card-black);
    overflow: hidden;
    box-shadow: 0 20px 40px rgba(0,0,0,.45);
  }

  /* Back side: company mark and general contact */
  .card-back {
    display: flex; flex-direction: column; align-items: center; justify-content: center;
  }
  .back-brand {
    font-family: "Montserrat", sans-serif; font-weight: 700;
    font-size: 64px; line-height: 1.05; text-align: center;
    color: var(--emboss-grey);
    margin-top: 40px;
  }
  .back-details {
    margin-top: 80px; text-align: center;
    font-family: "Roboto", sans-serif; font-size: 18px;
    color: var(--muted-grey); line-height: 1.4;
  }
  .back-details .dot {
    display: inline-block; width: 6px; height: 6px; border-radius: 50%;
    background: var(--brand-red); vertical-align: middle; margin: 0 8px 4px;
  }

  /* Front side: person details */
  .front-brand {
    position: absolute; left: 70px; top: 120px; width: 270px;
    font-family: "Montserrat", sans-serif; font-weight: 700;
    font-size: 50px; line-height: 1.02;
    color: var(--brand-red);
  }
  .front-divider {
    position: absolute; left: 368px; top: 118px;
    width: 2px; height: 200px; background: var(--brand-red);
  }
  .person {
    position: absolute; left: 400px; top: 124px;
  }
  .person-name {
    font-family: "Montserrat", sans-serif; font-weight: 700;
    font-size: 36px; color: var(--brand-red); line-height: 1.1;
  }
  .person-title {
    font-family: "Roboto", sans-serif; font-size: 20px;
    color: var(--text-white); margin-top: 2px;
  }
  .contact-list { list-style: none; margin-top: 22px; }
  .contact-list li {
    display: flex; align-items: center; gap: 12px;
    font-family: "Roboto", sans-serif; font-size: 19px;
    color: var(--text-white); margin-bottom: 11px;
  }
  .contact-icon { width: 22px; height: 22px; flex: none; }
  .card-wave { position: absolute; left: 0; bottom: 0; width: 860px; height: 491px; }
</style>
</head>
<body>
<main class="canvas">

  <section class="card card-back" aria-label="Card back">
    <div class="back-brand">Tandem Hearth<br>Works</div>
    <div class="back-details">
      <div><span class="dot"></span>Your FullCompanyName<span class="dot"></span></div>
      <div>123 456 7890 | youremail.com</div>
    </div>
  </section>

  <section class="card card-front" aria-label="Card front">
    <svg class="card-wave" viewBox="0 0 860 491" aria-hidden="true">
      <path d="M0,315 C180,380 420,400 600,408 C740,414 820,430 860,450 L860,491 L0,491 Z" fill="var(--wave-grey)"/>
      <path d="M0,335 C120,400 280,395 420,398 C600,402 760,430 860,470 L860,491 L0,491 Z" fill="var(--brand-red)"/>
      <path d="M0,328 C150,395 300,392 420,392" stroke="var(--card-black)" stroke-width="4" fill="none"/>
    </svg>

    <div class="front-brand">Tandem Hearth Works</div>
    <div class="front-divider"></div>

    <div class="person">
      <div class="person-name">Jonathan Doe</div>
      <div class="person-title">Founder &amp; CEO</div>
      <ul class="contact-list">
        <li>
          <svg class="contact-icon" viewBox="0 0 22 22" aria-hidden="true">
            <circle cx="11" cy="11" r="11" fill="var(--brand-red)"/>
            <path d="M7.5,6 L9.5,6 L10.3,8.6 L9,9.6 C9.7,11.2 10.8,12.3 12.4,13 L13.4,11.7 L16,12.5 L16,14.5 C16,15.3 15.3,16 14.5,16 C10.4,15.7 6.3,11.6 6,7.5 C6,6.7 6.7,6 7.5,6 Z" fill="#fff"/>
          </svg>
          +61 8 9000 0417
        </li>
        <li>
          <svg class="contact-icon" viewBox="0 0 22 22" aria-hidden="true">
            <circle cx="11" cy="11" r="11" fill="var(--brand-red)"/>
            <rect x="5.5" y="7" width="11" height="8" rx="1" fill="#fff"/>
            <path d="M5.8,7.4 L11,11.5 L16.2,7.4" stroke="var(--brand-red)" stroke-width="1.2" fill="none"/>
          </svg>
          ceo@tandemhearth.com
        </li>
        <li>
          <svg class="contact-icon" viewBox="0 0 22 22" aria-hidden="true">
            <circle cx="11" cy="11" r="11" fill="var(--brand-red)"/>
            <g stroke="#fff" stroke-width="1.2" fill="none">
              <circle cx="11" cy="11" r="5.5"/>
              <ellipse cx="11" cy="11" rx="2.4" ry="5.5"/>
              <line x1="5.5" y1="11" x2="16.5" y2="11"/>
            </g>
          </svg>
          www.tandemhearth.com
        </li>
      </ul>
    </div>
  </section>

</main>
</body>
</html>
```